Business Card Design For A Renovation Contractor Company

We need a business card for a new company based in Singapore, our company name is "RB Tolvane". We are a renovation contractor that builds designs into reality. We build more of F&B restaurants, retail stores and commercial offices. We work very closely with designers. The final design should communicate to our client that we are a company that you can trust, that will plan and complete your project without giving you a headache. I like my client to remember my company as "RB". The beauty of SIMPLE is important.

Industry/Entity Type

Contractor

Requirements
Nice to have
• Black or Red base

```html
<!DOCTYPE html>
<html lang="en">
<head>
<meta charset="utf-8">
<title>RB Tolvane – Business Card</title>
<link rel="stylesheet" href="https://fonts.googleapis.com/css2?family=Arimo:wght@400;700&family=Gelasio:wght@400;700&display=swap">
<style>
  :root {
    --stage: #d6d6d6;
    --stage-light: #ececec;
    --card: #f1f0ee;
    --ink: #1e1c1d;
    --grey: #6a6a6a;
    --red: #e0262c;
    --rule: #444;
  }
  * { box-sizing: border-box; margin: 0; padding: 0; }
  html, body { width: 1200px; height: 900px; overflow: hidden; }
  body {
    background: linear-gradient(180deg, var(--stage) 0%, var(--stage-light) 100%);
    font-family: "Arimo", Arial, sans-serif;
    position: relative;
  }
  .card {
    position: absolute;
    top: 300px;
    width: 525px;
    height: 300px;
    background: var(--card);
    border-radius: 26px;
    box-shadow: 0 10px 28px rgba(0,0,0,0.18);
    overflow: hidden;
  }
  .card--front { left: 50px; }
  .card--back { left: 625px; }

  /* Front */
  .slogan {
    position: absolute;
    left: 120px;
    top: 66px;
    color: var(--ink);
    line-height: 0.9;
  }
  .slogan__small { font-size: 30px; display: block; }
  .slogan__large { font-size: 72px; display: block; letter-spacing: -1px; }
  .slogan__row { display: flex; align-items: flex-end; gap: 12px; }
  .slogan__row .slogan__small { padding-bottom: 14px; }
  .web {
    position: absolute;
    left: 248px;
    top: 252px;
    font-family: "Gelasio", Georgia, serif;
    font-weight: 700;
    font-size: 15px;
    color: var(--ink);
  }
  .web__name { color: var(--red); }

  /* Back */
  .marker {
    position: absolute;
    left: -10px;
    top: 62px;
    width: 20px;
    height: 20px;
    border-radius: 50%;
    background: var(--red);
  }
  .holder {
    position: absolute;
    left: 38px;
    top: 60px;
    font-family: "Gelasio", Georgia, serif;
  }
  .holder__name { font-size: 19px; color: var(--grey); letter-spacing: 0.3px; }
  .holder__role { font-size: 15px; color: var(--red); margin-top: 2px; }
  .contacts {
    position: absolute;
    left: 40px;
    top: 150px;
    list-style: none;
    font-family: "Gelasio", Georgia, serif;
    font-size: 14px;
    color: var(--grey);
    line-height: 19px;
  }
  .contacts li { display: flex; align-items: flex-start; gap: 10px; }
  .contacts svg { width: 12px; height: 12px; margin-top: 3px; flex: none; fill: var(--red); }
  .brand {
    position: absolute;
    right: 36px;
    top: 168px;
    text-align: left;
  }
  .brand__name {
    font-size: 40px;
    color: var(--ink);
    font-weight: 400;
    letter-spacing: -0.5px;
    line-height: 1;
  }
  .brand__tagline {
    margin-top: 4px;
    padding-top: 3px;
    border-top: 1px solid var(--rule);
    font-size: 15px;
    color: var(--ink);
    letter-spacing: 0.4px;
  }
</style>
</head>
<body>
  <section class="card card--front" aria-label="Business card front">
    <p class="slogan">
      <span class="slogan__small">crafting</span>
      <span class="slogan__large">spaces</span>
      <span class="slogan__row">
        <span class="slogan__small">built to</span>
        <span class="slogan__large">last</span>
      </span>
    </p>
    <p class="web">www.<span class="web__name">RBtolvane.com</span></p>
  </section>

  <section class="card card--back" aria-label="Business card back">
    <span class="marker"></span>
    <div class="holder">
      <p class="holder__name">CARDHOLDER NAME</p>
      <p class="holder__role">Designation</p>
    </div>
    <ul class="contacts">
      <li>
        <svg viewBox="0 0 12 12" aria-hidden="true"><path d="M6 0a4 4 0 0 0-4 4c0 3 4 8 4 8s4-5 4-8a4 4 0 0 0-4-4zm0 5.6A1.6 1.6 0 1 1 6 2.4a1.6 1.6 0 0 1 0 3.2z"/></svg>
        <span>01 01 Avenue, Suite No. 123<br>Your City, Country</span>
      </li>
      <li>
        <svg viewBox="0 0 12 12" aria-hidden="true"><circle cx="6" cy="6" r="6"/><path d="M4 3l1 1.5-.7.8a4 4 0 0 0 2.4 2.4l.8-.7L9 8l-.8 1A5 5 0 0 1 3 3.8z" fill="#fff"/></svg>
        <span>012 345 6789</span>
      </li>
      <li>
        <svg viewBox="0 0 12 12" aria-hidden="true"><rect x="3" y="0" width="6" height="4"/><rect x="0" y="5" width="12" height="5" rx="1"/><rect x="3" y="8" width="6" height="4"/></svg>
        <span>012 345 6780</span>
      </li>
      <li>
        <svg viewBox="0 0 12 12" aria-hidden="true"><rect x="0" y="2" width="12" height="8" rx="1"/><path d="M1 3l5 3.5L11 3" stroke="#fff" fill="none"/></svg>
        <span>name@rbtolvane.com</span>
      </li>
    </ul>
    <div class="brand">
      <p class="brand__name">RB Tolvane</p>
      <p class="brand__tagline">crafting spaces built to last</p>
    </div>
  </section>
</body>
</html>
```